New business card/stationary for a consulting company

I am looking for a clean and very professional looking business card for my consulting company as well as corresponding stationary. I am uploading our logo. I like simple and powerful for the feel. No graphics but I am open on everything else. Below is my contact information but would like the final to be in a version I can add my employees information into and print. Thank you.

Daniel Whitcombe
dan@ferncliffadvisory.com
2870 North 9th Avenue, Summit Floor, Elm Ridge, Illinois 60531
www.ferncliffadvisory.com

Industry/Entity Type

Consulting

Contact Information for Business Card

Daniel Whitcombe
dan@ferncliffadvisory.com
www.ferncliffadvisory.com

Font styles to use
Serif
Sans Serif

Requirements
Must have
• Our logo and the business card details.
Nice to have
• our website www.ferncliffadvisory.com

```html
<!DOCTYPE html>
<html lang="en">
<head>
<meta charset="utf-8">
<title>Ferncliff Advisory — Stationery</title>
<link href="https://fonts.googleapis.com/css2?family=Questrial&family=Arimo:wght@400;700&display=swap" rel="stylesheet">
<style>
  :root{
    --navy:#03005f;
    --navy-deep:#02004c;
    --paper:#f1f1f1;
    --backdrop:#d2d2d2;
    --ink:#222;
    --ink-soft:#555;
  }
  *{margin:0;padding:0;box-sizing:border-box}
  html,body{width:1200px;height:1041px;overflow:hidden;background:var(--backdrop)}
  body{position:relative;font-family:"Questrial",sans-serif}
  .piece{position:absolute;overflow:hidden}
  .brand{position:absolute;left:0;right:0;text-align:center;font-family:"Questrial",sans-serif;color:var(--navy);letter-spacing:.02em;white-space:nowrap}
  .brand-square{position:absolute;left:50%;transform:translateX(-50%);background:var(--navy)}
  .band{position:absolute;left:0;right:0;bottom:0;background:var(--navy)}

  /* Folder */
  .folder{left:166px;top:76px;width:417px;height:541px;background:var(--navy);border-radius:3px}
  .folder-spine{position:absolute;left:0;top:0;bottom:0;width:28px;background:var(--navy-deep);border-right:1px solid #0a0a78}
  .folder .brand-square{top:172px;width:30px;height:30px;background:var(--paper)}
  .folder .brand{top:214px;font-size:19px;color:#fff}
  .folder-url{position:absolute;left:0;right:0;top:573px;text-align:center;font-family:"Arimo",sans-serif;font-size:8px;color:#fff}
  .folder-url{top:497px}

  /* Letterhead */
  .letterhead{left:615px;top:95px;width:403px;height:522px;background:var(--paper)}
  .letterhead .brand-square{top:28px;width:20px;height:20px}
  .letterhead .brand{top:56px;font-size:12px}
  .letter{position:absolute;left:37px;top:168px;width:331px;font-size:5.6px;line-height:7px;color:var(--ink)}
  .letter p{text-align:justify;margin-bottom:4px}
  .letter .salutation{font-family:"Arimo",sans-serif;font-weight:700;margin-bottom:7px}
  .letter .closing{margin-top:14px;text-align:left}
  .letter .signer{font-family:"Arimo",sans-serif;font-weight:700}
  .signature{position:absolute;left:87px;top:337px;width:82px;height:44px;background:linear-gradient(135deg,#e6e9f5,#d5dbef);border-radius:3px}
  .letter-footer{position:absolute;left:0;right:0;top:501px;text-align:center;font-family:"Arimo",sans-serif;font-size:5.4px;color:var(--ink)}
  .letterhead .band{height:5px}

  /* Envelope front */
  .envelope-front{left:132px;top:645px;width:451px;height:196px;background:var(--paper)}
  .envelope-front .brand-square{left:87px;top:23px;width:16px;height:16px;transform:none}
  .envelope-front .brand{left:19px;right:auto;top:49px;font-size:12px;text-align:left}
  .return-address{position:absolute;left:40px;top:170px;width:88px;text-align:center;font-family:"Arimo",sans-serif;font-size:5.2px;line-height:6.3px;color:var(--ink)}
  .envelope-front .band{height:5px}

  /* Envelope back */
  .envelope-back{left:615px;top:645px;width:451px;height:196px;background:var(--paper)}
  .envelope-flap{position:absolute;left:0;top:0}
  .envelope-back .brand{top:29px;font-size:9px;color:#fff}

  /* Business cards */
  .card-front{left:417px;top:870px;width:167px;height:96px;background:var(--paper)}
  .card-front .brand-square{top:13px;width:10px;height:10px}
  .card-front .brand{top:30px;font-size:8px}
  .card-name{position:absolute;left:0;right:0;top:64px;text-align:center;font-family:"Arimo",sans-serif;font-weight:700;font-size:5px;color:var(--navy);letter-spacing:.02em}
  .card-contact{position:absolute;left:0;right:0;top:74px;text-align:center;font-family:"Arimo",sans-serif;font-size:3.6px;line-height:4.6px;color:var(--ink-soft)}
  .card-front .band{height:4px}

  .card-back{left:615px;top:870px;width:167px;height:96px;background:var(--navy)}
  .card-back .brand-square{top:28px;width:10px;height:10px;background:var(--paper)}
  .card-back .brand{top:49px;font-size:8px;color:#fff}
  .card-url{position:absolute;left:0;right:0;top:76px;text-align:center;font-family:"Arimo",sans-serif;font-size:3.8px;color:#fff}
</style>
</head>
<body>

<section class="piece folder" aria-label="Presentation folder">
  <div class="folder-spine"></div>
  <div class="brand-square"></div>
  <div class="brand">FERNCLIFF ADVISORY</div>
  <div class="folder-url">www.ferncliffadvisory.com</div>
</section>

<section class="piece letterhead" aria-label="Letterhead">
  <div class="brand-square"></div>
  <div class="brand">FERNCLIFF ADVISORY</div>
  <div class="letter">
    <p class="salutation">Dear sir,</p>
    <p>Thank you for the time you shared with our team last week. We value the chance to learn about your goals and the challenges your organization faces as it grows. This letter sets out how we would like to help and what the next steps could look like for both sides.</p>
    <p>Our work begins with a short review of your current operations, finances and market position. From there we build a clear plan with measurable targets, agreed timelines and a single point of contact. We report on progress every month, and we adjust the plan whenever the facts change. Our aim is simple: practical advice that your people can put to use from the first week, and results that last long after our engagement ends.</p>
    <p>Enclosed you will find a summary of our proposed scope, the team we would assign and an outline of fees. Every figure is open for discussion, and we are glad to tailor the proposal to fit your budget and calendar.</p>
    <p>Please call or write at any time with questions. We look forward to working with you and to building a lasting partnership.</p>
    <p class="closing">Yours Sincerely,<br><span class="signer">Lena Marsh</span></p>
  </div>
  <div class="signature" role="img" aria-label="Handwritten signature"></div>
  <div class="letter-footer">2870 North 9th Avenue, Summit Floor, Elm Ridge, Illinois 60531 &nbsp;/&nbsp; dan@ferncliffadvisory.com &nbsp;/&nbsp; www.ferncliffadvisory.com</div>
  <div class="band"></div>
</section>

<section class="piece envelope-front" aria-label="Envelope front">
  <div class="brand-square"></div>
  <div class="brand">FERNCLIFF ADVISORY</div>
  <div class="return-address">2870 North 9th Avenue, Summit Floor<br>Elm Ridge, Illinois 60531</div>
  <div class="band"></div>
</section>

<section class="piece envelope-back" aria-label="Envelope back">
  <svg class="envelope-flap" width="451" height="70" viewBox="0 0 451 70" aria-hidden="true">
    <path d="M0 0 H451 L437 58 Q434 64 427 64 H24 Q17 64 15 58 Z" fill="var(--navy)"/>
  </svg>
  <div class="brand">FERNCLIFF ADVISORY</div>
</section>

<section class="piece card-front" aria-label="Business card front">
  <div class="brand-square"></div>
  <div class="brand">FERNCLIFF ADVISORY</div>
  <div class="card-name">DANIEL WHITCOMBE</div>
  <div class="card-contact">dan@ferncliffadvisory.com &nbsp;/&nbsp; www.ferncliffadvisory.com<br>2870 North 9th Avenue, Summit Floor, Elm Ridge, Illinois 60531</div>
  <div class="band"></div>
</section>

<section class="piece card-back" aria-label="Business card back">
  <div class="brand-square"></div>
  <div class="brand">FERNCLIFF ADVISORY</div>
  <div class="card-url">www.ferncliffadvisory.com</div>
</section>

</body>
</html>
```